Market place for used airplanes/helicopters/parts

http://www.vingtorget.se needs a facelift.

# What is it
Classifieds for used airplanes/helicopters/parts/spare parts/aviation literature, for people in Scandinavia. The number of classifieds is ~120-200. They are mainly in Swedish, English, Norwegian.

It's not a glamorous or luxurious business, but more for people with a genuine interest in flying, technical things.

Similar to sites like this, but they have much more classifieds than my site
http://www.skyvendor.com/list/list.aspx?ETID=1&setype=1&catid=6
http://www.lindqvistflyg.com/planes.asp?meny=1&typ=single
https://www.hangarhub.com/cat.php?mode=listing&main=

# What I want
Design only - no code. I want a modern, maybe a bit bootstrap like, clean, simple, not flashy, web design. I want the design to be in English.

# Audience of the website
Aviation interested men, 45-65 years old, in the nordic countries (around Sweden).

# Logotype that could be used (but not necessarily)
http://www.vingtorget.se/flygplan_till_salu_large.jpg
http://www.vingtorget.se/flygplan_till_salu.eps

Reason: I decided to extend the deadline with 1 day. The reason is that I (unfortunately) managed to put the contest in the wrong category for 1 day + I want to give you all feedback (been too busy the whole day, sorry).

Hi all! 

Thanks everyone for the contributions you made. 

I will setup a poll for the designs that I like most. Will get back when I have more information. 

Thanks and have a nice weekend!
Erik

Target Market(s)

45-65 old Scandinavian men

Industry/Entity Type

Business

Requirements
Must have
• - A list with classifieds on the first page, so the visitor easily can see new classifieds.
- A classifieds should be able to have more than one photo
- A simple navigation for showing classifieds from categories like airplanes, helicopters/gyrocopters, parts, literature, misc (maybe other categories) .... but still, it's just 100-200 ads so it's not needed that much filtration.

- A placeholder/way of showing aviation news/clips. In the old design I had, it was a column to the right. It's enough to show maybe 2-5 placeholders.
- A placeholder for PlaceMint ads somewhere on the site.
Should not have
• - Carousels
- Too much clutter

```html
<!DOCTYPE html>
<html lang="en">
<head>
<meta charset="utf-8">
<title>Vingtorget – Aviation Classifieds</title>
<link rel="stylesheet" href="https://fonts.googleapis.com/css2?family=Source+Sans+3:wght@400;600;700;800&family=Arimo:wght@400&display=swap">
<style>
  :root {
    --ink: #333333;
    --title: #2c3a93;
    --hero-title: #2d3aa0;
    --accent: #1ea5cf;
    --accent-dark: #1487ad;
    --line: #e3e8ee;
    --nav-bg: #f7f8f9;
    --nav-border: #d6dade;
    --btn-bg: #f3f3f3;
    --btn-border: #c9c9c9;
    --sky-mid: #eef5fb;
    --page: #f8fbfe;
  }
  * { box-sizing: border-box; margin: 0; padding: 0; }
  html, body { width: 997px; height: 1200px; overflow: hidden; }
  body {
    position: relative;
    background: var(--page);
    font-family: "Source Sans 3", sans-serif;
    color: var(--ink);
  }
  .hero-sky {
    position: absolute; left: 0; top: 0; width: 997px; height: 402px;
    background:
      radial-gradient(ellipse 380px 160px at 180px 300px, rgba(190,220,240,.7), transparent),
      radial-gradient(ellipse 300px 140px at 860px 330px, rgba(190,220,240,.6), transparent),
      radial-gradient(ellipse 420px 120px at 500px 60px, rgba(200,225,242,.6), transparent),
      linear-gradient(180deg, var(--sky-mid) 0%, #e6f0f8 60%, #eaf3fa 100%);
    border-bottom: 1px solid #d3e3ef;
  }
  .logo {
    position: absolute; left: 170px; top: 38px;
    display: flex; align-items: center; gap: 6px;
    font-weight: 800; font-size: 23px; color: var(--hero-title);
    letter-spacing: -0.5px;
  }
  .logo-dot { width: 12px; height: 12px; border-radius: 50%; background: var(--accent); }
  .social { position: absolute; left: 748px; top: 5px; display: flex; gap: 3px; }
  .social span { width: 18px; height: 18px; border-radius: 50%; display: block; }
  .social .s1 { background: #3b5a99; }
  .social .s2 { background: #46b3e3; }
  .social .s3 { background: #f4a51f; }
  .social .s4 { background: #e86e2c; }
  .search {
    position: absolute; left: 664px; top: 42px; width: 167px; height: 20px;
    background: #fff; border: 1px solid #d4d9de; border-radius: 3px;
    font-size: 8px; color: #9aa3ab; padding: 5px 0 0 12px;
  }
  .search svg { position: absolute; right: 5px; top: 4px; }
  .main-nav {
    position: absolute; left: 165px; top: 77px; width: 666px; height: 27px;
    background: linear-gradient(#fdfdfd, var(--nav-bg));
    border: 1px solid var(--nav-border); border-radius: 3px;
    display: flex; font-size: 10px; color: #444;
  }
  .main-nav a {
    color: inherit; text-decoration: none; border-right: 1px solid var(--nav-border);
    display: flex; align-items: center; justify-content: center;
  }
  .main-nav a:last-child { border-right: 0; justify-content: flex-start; padding-left: 11px; flex: 1; }
  .plane-art {
    position: absolute; left: 632px; top: 132px; width: 198px; height: 80px;
    border-radius: 40px;
    background: linear-gradient(160deg, rgba(255,255,255,.9), rgba(200,210,220,.6));
  }
  .hero-title {
    position: absolute; left: 0; top: 196px; width: 997px; text-align: center;
    font-weight: 800; font-size: 50px; line-height: 41px; letter-spacing: -2.6px;
    color: var(--hero-title); text-transform: uppercase;
  }
  .hero-lead {
    position: absolute; left: 260px; top: 284px; width: 480px; text-align: center;
    font-size: 9.5px; line-height: 12px; color: #333;
  }
  .hero-cta {
    position: absolute; left: 426px; top: 336px; width: 142px; height: 33px;
    background: var(--accent); border: 1px solid var(--accent-dark); border-radius: 3px;
    color: #fff; font-size: 15px; text-align: center; line-height: 31px;
  }
  .listings {
    position: absolute; left: 165px; top: 418px; width: 558px;
    display: grid; grid-template-columns: 288px 270px; grid-auto-rows: 173px;
  }
  .listing { position: relative; border-bottom: 1px solid var(--line); padding-top: 2px; }
  .listing:nth-child(odd) { padding-right: 17px; border-right: 1px solid var(--line); }
  .listing:nth-child(even) { padding-left: 25px; }
  .listing h2 {
    font-weight: 600; font-size: 16px; color: var(--title); letter-spacing: -0.4px;
    margin-bottom: 12px; white-space: nowrap;
  }
  .listing-body { display: flex; gap: 6px; }
  .thumb { flex: 0 0 95px; height: 70px; border: 2px solid #d6d6d6; }
  .listing-text { font-size: 8.6px; line-height: 12px; color: #333; }
  .listing-text strong { font-weight: 600; display: block; }
  .view-btn {
    position: absolute; bottom: 33px; height: 20px; width: 75px;
    background: linear-gradient(#fff, var(--btn-bg)); border: 1px solid var(--btn-border);
    border-radius: 2px; font-family: "Arimo", sans-serif; font-size: 8.6px; color: #555;
    text-align: center; line-height: 18px;
  }
  .listing:nth-child(odd) .view-btn { right: 17px; }
  .listing:nth-child(even) .view-btn { right: 5px; }
  .ad-column { position: absolute; left: 750px; top: 441px; width: 80px; }
  .ad { display: block; width: 80px; margin-bottom: 16px; }
  .footer-rule { position: absolute; left: 165px; top: 1152px; width: 666px; height: 4px; background: var(--accent); }
  .footer-nav {
    position: absolute; left: 0; top: 1161px; width: 997px; text-align: center;
    font-size: 10.5px; color: #444; word-spacing: 1px;
  }
  .footer-nav a { color: inherit; text-decoration: none; margin: 0 3px; }
  .copyright {
    position: absolute; left: 0; top: 1179px; width: 997px; text-align: center;
    font-size: 7.5px; color: #555;
  }
</style>
</head>
<body>
  <div class="hero-sky"></div>

  <header>
    <div class="logo"><span class="logo-dot"></span>VINGTORGET</div>
    <div class="social"><span class="s1"></span><span class="s2"></span><span class="s3"></span><span class="s4"></span></div>
    <div class="search">Search Key Words
      <svg width="10" height="10" viewBox="0 0 10 10"><circle cx="6" cy="4" r="3" fill="none" stroke="#1a7fb8" stroke-width="1.4"/><line x1="4" y1="6" x2="1" y2="9" stroke="#1a7fb8" stroke-width="1.6"/></svg>
    </div>
    <nav class="main-nav">
      <a style="width:47px">Home</a>
      <a style="width:61px">Airplanes</a>
      <a style="width:124px">Helicopters/gyrocopters</a>
      <a style="width:44px">Help</a>
      <a style="width:47px">Events</a>
      <a style="width:44px">Parts</a>
      <a style="width:62px">Literature</a>
      <a style="width:66px">Classifieds</a>
      <a>Misc</a>
    </nav>
  </header>

  <section class="hero">
    <div class="plane-art" role="img" aria-label="White business jet in flight"></div>
    <h1 class="hero-title">Ipsum generators on<br>the internet tend.</h1>
    <p class="hero-lead">Cras justo odio, dapibus ac facilisis in, egestas eget quam. Fusce dapibus, tellus ac cursus commodo, tortor mauris condimentum nibh, ut fermentum massa justo sit amet risus.</p>
    <div class="hero-cta">Perchase Now</div>
  </section>

  <main class="listings">
    <article class="listing">
      <h2>Vacuum pump</h2>
      <div class="listing-body">
        <div class="thumb" role="img" aria-label="Photo of a vacuum pump" style="background:linear-gradient(135deg,#8b8b8b,#cfcfcf)"></div>
        <div class="listing-text"><strong>Avionic Supply, TT 222 hrs, price 1200 SEK</strong>Name: Nils-Åke, Email<br>Phone: 0701-555012<br>Date: 2013-10-05 19:31:18</div>
      </div>
      <div class="view-btn">View details »</div>
    </article>
    <article class="listing">
      <h2>Aerovik MX ULC</h2>
      <div class="listing-body">
        <div class="thumb" role="img" aria-label="Photos of an ultralight aircraft and its cockpit" style="background:linear-gradient(135deg,#6a6f75,#b9bcc0)"></div>
        <div class="listing-text"><strong>Aerovik MX ULC</strong>A unique UL machine in carbon fiber, it makes it exceptionally easy. Empty weight 268kg<br>Manuf. 2006 ca.260 hours, always in hangar.</div>
      </div>
      <div class="view-btn">View details »</div>
    </article>
    <article class="listing">
      <h2>Aerobatic Rallon S-9B LN-XQA</h2>
      <div class="listing-body">
        <div class="thumb" role="img" aria-label="Aerial photo of an aerobatic plane over an airfield" style="background:linear-gradient(135deg,#6f7b70,#a9aeb0)"></div>
        <div class="listing-text">Experimental clipped wing +9/-6G airshow performer for sale in Norway.<br>Phone: +4790000123<br>Date: 2013-10-04 12:23:08</div>
      </div>
      <div class="view-btn">View details »</div>
    </article>
    <article class="listing">
      <h2>Pilan Sparrow 140 Auto STC</h2>
      <div class="listing-body">
        <div class="thumb" role="img" aria-label="Single engine plane on a runway" style="height:40px;background:linear-gradient(180deg,#a8b9c6,#8a8f7d)"></div>
        <div class="listing-text">Experimental clipped wing +9/-6G airshow performer for sale in Norway.<br>Phone: +4790000123<br>Date: 2013-10-04 12:23:08</div>
      </div>
      <div class="view-btn">View details »</div>
    </article>
    <article class="listing">
      <h2>LN XKT FR170J 1973 Salg wil!</h2>
      <div class="listing-body">
        <div class="thumb" role="img" aria-label="Floatplane moored by a bridge" style="height:60px;background:linear-gradient(180deg,#8fa0ae,#3f5b5a)"></div>
        <div class="listing-text">We shell reach prave the selge our Cestra 170 varnes rapid 210hp. fluke are on nylakkerte floats.<br>Phone: +4790000123<br>Date: 2013-10-04 12:23:08</div>
      </div>
      <div class="view-btn">View details »</div>
    </article>
    <article class="listing">
      <h2>Mauder M6-82/89</h2>
      <div class="listing-body">
        <div class="thumb" role="img" aria-label="Floatplane on a lake at dusk" style="background:linear-gradient(180deg,#aab6c8,#4c5a6c)"></div>
        <div class="listing-text">Mauder ML6-235, vm. 1982 brought to Finland in 1989.<br><br>Name: Jarmo, Email Phone: +358-40-5550188 Date: 2013-09-30 15:21:59</div>
      </div>
      <div class="view-btn">View details »</div>
    </article>
    <article class="listing">
      <h2>Aerobatic Rallon S-9B LN-XQA</h2>
      <div class="listing-body">
        <div class="thumb" role="img" aria-label="Hangar doors" style="background:linear-gradient(180deg,#c7ccd0,#8a8770)"></div>
        <div class="listing-text">A place is vacant for a smaller lågvingad plan in our large hangar with 18x4 meter opening.<br>Name: Arvid, Email<br>Phone: 070-555 12 34 0515-555 60<br>Date: 2013-09-30 10:07:15</div>
      </div>
      <div class="view-btn">View details »</div>
    </article>
    <article class="listing">
      <h2>Aluminum Floats from Jonas Fellberg.</h2>
      <div class="listing-body">
        <div class="thumb" role="img" aria-label="Aluminum floats in a workshop" style="background:linear-gradient(135deg,#d8d8d2,#9b9890)"></div>
        <div class="listing-text">New 1450 lbs floats built by Jonas Fellberg. Made with pack slots in two floats.<br>Name: Maria Holmgren, Email<br>Phone: 070-5550457<br>Date: 2013-09-29 18:18:52</div>
      </div>
      <div class="view-btn">View details »</div>
    </article>
  </main>

  <aside class="ad-column">
    <div class="ad" role="img" aria-label="Advertisement for model batteries" style="height:159px;background:linear-gradient(180deg,#1d2a52,#0b0b14)"></div>
    <div class="ad" role="img" aria-label="Advertisement for model batteries" style="height:160px;background:linear-gradient(180deg,#f3f3f3,#d83a35)"></div>
    <div class="ad" role="img" aria-label="Advertisement for hobby tools" style="height:158px;background:linear-gradient(180deg,#c9ccd0,#111)"></div>
    <div class="ad" role="img" aria-label="Advertisement for a radio control transmitter" style="height:158px;background:linear-gradient(180deg,#e07a1c,#a63d12)"></div>
  </aside>

  <footer>
    <div class="footer-rule"></div>
    <nav class="footer-nav"><a>Home</a><a>Copyright &amp; Legal Notice</a><a>Privacy Policy</a><a>Site Map</a><a>Contact Us</a></nav>
    <p class="copyright">Copyright © by vingtorget 2013. All rights reserved.</p>
  </footer>
</body>
</html>
```